Business Card Design for Software Development Company

I am looking for a business card design the incorporates my new logo (attached below).

Key information to include:
Name: Martin Quelbrook
Title: CEO
Email: martin@brightwellcivic.example
Phone: 555-218-9403
Website: www.brightwellcivic.example

NOTE: This design should be easy to edit so that we can order cards for different members of our team.

```html
<!DOCTYPE html>
<html lang="en">
<head>
<meta charset="UTF-8">
<title>Brightwell Labs — Business Card</title>
<link rel="stylesheet" href="https://fonts.googleapis.com/css2?family=Montserrat:wght@400;600;700&display=swap">
<style>
  :root {
    --bg: #e3e1e2;
    --card-white: #ffffff;
    --brand-orange: #e8803a;
    --brand-slate: #68728e;
    --brand-periwinkle: #6f7a9c;
    --ink-navy: #363c5a;
    --ink-dark: #1f2230;
    --shadow: 0 10px 22px rgba(40, 40, 50, 0.28);
  }
  * { box-sizing: border-box; margin: 0; padding: 0; }
  html, body {
    width: 1200px;
    height: 1108px;
    overflow: hidden;
    background: var(--bg);
    font-family: "Montserrat", Arial, sans-serif;
  }
  .canvas { position: relative; width: 1200px; height: 1108px; }

  .card { position: absolute; box-shadow: var(--shadow); overflow: hidden; }

  /* Front */
  .card-front { left: 229px; top: 56px; width: 755px; height: 461px; background: var(--card-white); }
  .front-wordmark {
    position: absolute; left: 88px; top: 241px;
    display: flex; align-items: center; gap: 9px;
  }
  .wordmark-square { width: 22px; height: 22px; background: var(--brand-orange); }
  .wordmark-name {
    font-weight: 700; color: var(--ink-navy);
    font-size: 30px; letter-spacing: -0.5px; line-height: 1;
  }
  .front-divider {
    position: absolute; left: 373px; top: 178px;
    width: 2px; height: 147px; background: var(--brand-orange);
  }
  .contact-block { position: absolute; left: 389px; top: 178px; color: var(--ink-dark); }
  .contact-name { font-weight: 600; font-size: 29px; color: var(--brand-orange); line-height: 1.1; letter-spacing: 0.2px; }
  .contact-title { font-size: 16px; margin-top: 4px; line-height: 1.2; }
  .contact-list { list-style: none; margin-top: 8px; }
  .contact-list li {
    display: flex; align-items: center; gap: 8px;
    font-size: 17px; line-height: 29.5px;
  }
  .contact-list svg { width: 15px; height: 15px; flex: none; }

  .front-band { position: absolute; left: 0; bottom: 0; width: 755px; height: 25px; }

  /* Back */
  .card-back { left: 228px; top: 575px; width: 755px; height: 444px; background: var(--brand-periwinkle); }
  .back-wordmark {
    position: absolute; left: 0; right: 0; top: 200px;
    display: flex; justify-content: center; align-items: center; gap: 14px;
  }
  .back-wordmark .wordmark-square { width: 34px; height: 34px; }
  .back-wordmark .wordmark-name { font-size: 50px; letter-spacing: -1px; color: var(--ink-navy); }
</style>
</head>
<body>
<main class="canvas">

  <section class="card card-front" aria-label="Business card front">
    <div class="front-wordmark">
      <span class="wordmark-square"></span>
      <span class="wordmark-name">Brightwell Labs</span>
    </div>

    <div class="front-divider"></div>

    <div class="contact-block">
      <p class="contact-name">Martin Quelbrook</p>
      <p class="contact-title">CEO</p>
      <ul class="contact-list">
        <li>
          <svg viewBox="0 0 16 16" aria-hidden="true"><path fill="var(--brand-orange)" d="M3.6 1.5l2.3 2.6-1.4 1.8c.9 2 2.6 3.7 4.6 4.6l1.8-1.4 2.6 2.3-1.3 2.4C6.7 13.6 2.4 9.3 1.2 3.8z"/></svg>
          <span>555-218-9403</span>
        </li>
        <li>
          <svg viewBox="0 0 16 16" aria-hidden="true"><rect x="1.5" y="3.5" width="13" height="9.5" fill="var(--brand-orange)"/><path d="M1.5 3.8L8 8.6l6.5-4.8" fill="none" stroke="#fff" stroke-width="1.3"/></svg>
          <span>martin@brightwellcivic.example</span>
        </li>
        <li>
          <svg viewBox="0 0 16 16" aria-hidden="true"><circle cx="8" cy="8" r="6.8" fill="var(--brand-orange)"/><path d="M1.4 8h13.2M8 1.2c2.2 2 2.2 11.6 0 13.6M8 1.2c-2.2 2-2.2 11.6 0 13.6" fill="none" stroke="#fff" stroke-width="1"/></svg>
          <span>www.brightwellcivic.example</span>
        </li>
      </ul>
    </div>

    <svg class="front-band" viewBox="0 0 755 25" preserveAspectRatio="none" aria-hidden="true">
      <polygon points="0,0 393,0 375,25 0,25" fill="var(--brand-slate)"/>
      <polygon points="405,0 755,0 755,25 387,25" fill="var(--brand-orange)"/>
    </svg>
  </section>

  <section class="card card-back" aria-label="Business card back">
    <div class="back-wordmark">
      <span class="wordmark-square"></span>
      <span class="wordmark-name">Brightwell Labs</span>
    </div>
  </section>

</main>
</body>
</html>
```